Soy Candle Labels

We sell soy candles in recycled wine bottles. The wine bottle is cut in half and filled with pure and natural soy wax and scented with essential oils.
Our product represents good use of up cycling materials for a better use. The product is all natural and eco friendly.
You can see good use of labels and branding for a company in America that does the same thing http://larkmeadow7wicks.example/
Trya dn keep the label uncomplicated like the above labels.
We will need an area to hand stamp the scent. Similar to the labels used on the above website.
We would prefer to use a white or off white paper label with gold or bronze printing - limit the use of colour and keep the label simple and sophisticated.
Emberlace Candle Co. is our company name. Emberlace being the predominant name and candle co. written small underneath right justified.
Die cut labels might look better than a rectangle.
Dimensions should be 90mm Wide x 90mm High
The final design should communicate a professional and quality product. But stay modern and professional. Clean, elegant and sophisticated.
Can use wording such as: Hand Poured, Premium Soy Wax, All Natural, Up cycled
Have a look at the attached image for the look and feel we are going for.
Updates
Designers are having a little bit of trouble interpreting the brief into a viable design. To assist perhaps you can look at WINE LABELS on google images. Design your label around an existing style wine label to give the canld ethe feel of being a bottle of wine. Get creative! :)
Reason: We require more designs. We havnt quite got what were looking for.
Please see brief.

```html
<!DOCTYPE html>
<html lang="en">
<head>
<meta charset="utf-8">
<title>Emberlace Candle Co. — Soy Candle Label</title>
<link rel="stylesheet" href="https://fonts.googleapis.com/css2?family=Hind:wght@400;500&family=Oswald:wght@300&display=swap">
<style>
  :root {
    --gold: #a8872f;
    --paper: #fdfcf6;
    --bronze-dark: #3a1c0e;
    --ink: #3a1c0e;
  }
  html, body {
    margin: 0;
    padding: 0;
    width: 1200px;
    height: 1000px;
    overflow: hidden;
    background: var(--gold);
  }
  .canvas {
    position: relative;
    width: 1200px;
    height: 1000px;
    background: var(--gold);
  }
  .label {
    position: absolute;
    left: 168px;
    top: 74px;
    width: 880px;
    height: 879px;
    background: var(--paper);
    border-radius: 22px;
    overflow: hidden;
    color: var(--ink);
    font-family: "Hind", Arial, sans-serif;
  }
  .label__band {
    position: absolute;
    left: 0;
    top: 0;
    width: 100%;
    height: 34px;
    background: var(--bronze-dark);
  }
  .claims {
    position: absolute;
    left: 43px;
    top: 62px;
    margin: 0;
    line-height: 1;
  }
  .claims__title {
    display: block;
    font-size: 40px;
    font-weight: 500;
    margin-bottom: 10px;
  }
  .claims__line {
    display: block;
    font-size: 28px;
    font-weight: 500;
    margin-bottom: 8px;
  }
  .claims__line--small {
    font-size: 25px;
  }
  .scent-stamp {
    position: absolute;
    right: 50px;
    top: 70px;
    width: 24px;
    font-size: 27px;
    line-height: 27px;
    text-align: center;
    font-weight: 400;
    letter-spacing: 0;
  }
  .scent-stamp span { display: block; }
  .brand {
    position: absolute;
    right: 60px;
    top: 340px;
    text-align: right;
  }
  .brand__name {
    display: block;
    font-size: 150px;
    font-weight: 400;
    line-height: 1;
    letter-spacing: 1px;
  }
  .brand__sub {
    display: block;
    font-size: 30px;
    font-weight: 400;
    line-height: 1;
    margin-top: 8px;
    margin-right: 14px;
  }
  .footer-note {
    position: absolute;
    bottom: 56px;
    font-family: "Oswald", "Arial Narrow", sans-serif;
    font-weight: 300;
    font-size: 42px;
    line-height: 1;
    transform: scaleX(0.86);
  }
  .footer-note--origin { left: 44px; transform-origin: left bottom; }
  .footer-note--material { right: 42px; transform-origin: right bottom; }
</style>
</head>
<body>
  <div class="canvas">
    <section class="label">
      <div class="label__band"></div>

      <p class="claims">
        <span class="claims__title">Hand Poured</span>
        <span class="claims__line">All Natural Soy</span>
        <span class="claims__line claims__line--small">320 gm of Premium Soy Wax</span>
      </p>

      <div class="scent-stamp" aria-label="Scent">
        <span>S</span><span>C</span><span>E</span><span>N</span><span>T</span>
      </div>

      <div class="brand">
        <span class="brand__name">Emberlace</span>
        <span class="brand__sub">Candle Co.</span>
      </div>

      <div class="footer-note footer-note--origin">Product of Australia</div>
      <div class="footer-note footer-note--material">Up-Cycled wine bottle</div>
    </section>
  </div>
</body>
</html>
```